Maple Gable Business Card

Colors can be blue, grey and white as you see in the attached logo. Needs to have a spot for name, title, phone, email, address, and website. There also needs to be a spot for an agent's picture.

Contact Information for Business Card

See project description.

Colors

Designer to choose colors to be used in the design.

```html
<!DOCTYPE html>
<html lang="en">
<head>
<meta charset="utf-8">
<title>Maple Gable Business Card</title>
<link href="https://fonts.googleapis.com/css2?family=Montserrat:wght@400;500;700&display=swap" rel="stylesheet">
<style>
  :root {
    --backdrop: #4a4540;
    --brand-blue: #3a7bc1;
    --card-blue: #3478bb;
    --emboss-blue: #2e6aa6;
    --ink-grey: #3d3d40;
    --rule-grey: #2c2c2e;
    --photo-tone: #c9d6e4;
    --paper: #ffffff;
  }
  * { box-sizing: border-box; margin: 0; padding: 0; }
  html, body { width: 1200px; height: 930px; overflow: hidden; }
  body {
    background: var(--backdrop);
    font-family: "Montserrat", sans-serif;
    position: relative;
  }
  .card {
    position: absolute;
    width: 560px;
    height: 320px;
    border-radius: 22px;
    box-shadow: 0 14px 30px rgba(0,0,0,0.35);
  }
  .card-back {
    left: 80px; top: 110px;
    background: var(--card-blue);
    display: flex; align-items: center; justify-content: center;
  }
  .back-wordmark {
    display: flex; align-items: center; gap: 12px;
    color: var(--emboss-blue);
    font-weight: 700; font-size: 34px; letter-spacing: 1px;
    text-transform: uppercase;
  }
  .back-wordmark .mark-square { width: 26px; height: 26px; background: var(--emboss-blue); }
  .card-front {
    left: 560px; top: 480px;
    background: var(--paper);
  }
  .agent-photo {
    position: absolute; left: 40px; top: 34px;
    width: 86px; height: 86px; border-radius: 50%;
    background: linear-gradient(160deg, #dbe5ef, var(--photo-tone));
    border: 2px solid var(--brand-blue);
  }
  .front-wordmark {
    position: absolute; right: 36px; top: 48px;
    display: flex; align-items: center; gap: 10px;
    color: var(--brand-blue);
    font-weight: 700; font-size: 28px; letter-spacing: 0.5px;
    text-transform: uppercase;
  }
  .front-wordmark .mark-square { width: 20px; height: 20px; background: var(--brand-blue); }
  .top-rule {
    position: absolute; left: 230px; right: 36px; top: 112px;
    border-top: 1.5px solid var(--rule-grey);
  }
  .agent { position: absolute; left: 40px; top: 138px; }
  .agent-name {
    color: var(--brand-blue);
    font-weight: 700; font-size: 21px; letter-spacing: 0.5px;
    text-transform: uppercase;
  }
  .agent-title { color: var(--ink-grey); font-size: 14px; margin-top: 2px; }
  .mid-rule {
    position: absolute; left: 40px; width: 270px; top: 194px;
    border-top: 1.5px solid var(--rule-grey);
  }
  .contact-list { position: absolute; left: 40px; top: 204px; list-style: none; }
  .contact-list li {
    display: flex; align-items: center; gap: 9px;
    color: var(--ink-grey); font-size: 14px; line-height: 22px;
  }
  .contact-list svg { width: 13px; height: 13px; fill: none; stroke: var(--brand-blue); stroke-width: 2; flex: none; }
  .contact-list .accent { color: var(--brand-blue); }
</style>
</head>
<body>
  <div class="card card-back">
    <div class="back-wordmark"><span class="mark-square"></span>Maple Gable</div>
  </div>

  <div class="card card-front">
    <div class="agent-photo" role="img" aria-label="Agent portrait photo"></div>
    <div class="front-wordmark"><span class="mark-square"></span>Maple Gable</div>
    <div class="top-rule"></div>

    <div class="agent">
      <div class="agent-name">Daniel Whitaker</div>
      <div class="agent-title">Director</div>
    </div>
    <div class="mid-rule"></div>

    <ul class="contact-list">
      <li>
        <svg viewBox="0 0 24 24"><path d="M5 3h4l2 5-3 2a12 12 0 0 0 6 6l2-3 5 2v4a2 2 0 0 1-2 2A18 18 0 0 1 3 5a2 2 0 0 1 2-2z"/></svg>
        (555) 018-2746
      </li>
      <li>
        <svg viewBox="0 0 24 24"><rect x="3" y="5" width="18" height="14" rx="1"/><path d="M3 6l9 7 9-7"/></svg>
        info@maplegable.com
      </li>
      <li>
        <svg viewBox="0 0 24 24"><path d="M12 22s7-7 7-12a7 7 0 0 0-14 0c0 5 7 12 7 12z"/><circle cx="12" cy="10" r="2.5"/></svg>
        214 Linden Avenue, Springfield
      </li>
      <li>
        <svg viewBox="0 0 24 24"><circle cx="12" cy="12" r="9"/><path d="M3 12h18M12 3c3 3 3 15 0 18M12 3c-3 3-3 15 0 18"/></svg>
        <span>www.<span class="accent">maplegable</span>.com</span>
      </li>
    </ul>
  </div>
</body>
</html>
```